I have a logo and need to design the business card and stationery.
Updates

The uploaded logo image named as GREYMARSH CONSTRUCTION which is to be replaced to GREYMARSH CONTRACTS. Kindly add below details and submit the designs- Company name- Greymarsh Engineering Contracts LLP Name & Post- Kelvan Joshi (Designated Partner) Address- Block No.317, Wing C, Tulvo Trade Court, Manek Pural Road, Ruparel Industrial Estate, Goregaon(E), Mumbai - 400 063 Contact- +91 97415 60382 Email- kelvanjoshi@mailbrook.example Website- www.greymarshcontracts.example Contact for Letterhead- +91-22-28754193

Hi Tovin Rahul, We are liking your Design #28860835. We have suggested some changes which are mentioned in feedback. Kindly revert with it asap to finalize this design.

Colors

Designer to choose colors to be used in the design.

```html
<!DOCTYPE html>
<html lang="en">
<head>
<meta charset="utf-8">
<title>Greymarsh Contracts – Business Card</title>
<link href="https://fonts.googleapis.com/css2?family=Arimo:wght@400;700&display=swap" rel="stylesheet">
<style>
  :root {
    --backdrop: #e4e4e4;
    --card-white: #ffffff;
    --band-dark: #333333;
    --block-grey: #777777;
    --ink: #2e2e2e;
    --ink-soft: #5a5a5a;
    --card-black: #262626;
    --pattern-tone: #303030;
    --on-dark: #f4f4f4;
  }
  * { margin: 0; padding: 0; box-sizing: border-box; }
  html, body { width: 1200px; height: 802px; overflow: hidden; }
  body {
    background: var(--backdrop);
    font-family: "Arimo", Arial, sans-serif;
    position: relative;
  }
  .card {
    position: absolute;
    top: 246px;
    width: 540px;
    height: 310px;
    overflow: hidden;
    box-shadow: 0 6px 18px rgba(0,0,0,0.18);
  }
  /* Front */
  .card-front { left: 40px; background: var(--card-white); }
  .name-band {
    position: absolute; left: 0; top: 22px;
    width: 380px; height: 78px;
    background: var(--band-dark);
    padding: 22px 0 0 30px;
    color: var(--on-dark);
  }
  .holder-name { font-size: 17px; font-weight: 700; letter-spacing: 0.5px; }
  .holder-title { font-size: 12px; margin-top: 4px; }
  .brand-square {
    position: absolute; left: 396px; top: 34px;
    width: 52px; height: 52px;
    border: 5px solid var(--band-dark);
  }
  .grey-block {
    position: absolute; left: 462px; top: 22px;
    width: 78px; height: 58px;
    background: var(--block-grey);
  }
  .company-name {
    position: absolute; right: 26px; top: 108px;
    text-align: right; color: var(--ink); font-weight: 700;
  }
  .company-name .main { font-size: 22px; letter-spacing: 0.5px; display: block; line-height: 24px; }
  .company-name .sub { font-size: 10px; letter-spacing: 6.4px; margin-right: -6.4px; display: block; margin-top: 3px; line-height: 12px; }
  .address {
    position: absolute; right: 26px; top: 162px;
    text-align: right; font-size: 11px; line-height: 15px; color: var(--ink-soft);
    font-style: normal;
  }
  .address .firm { font-weight: 700; color: var(--ink); display: block; margin-bottom: 2px; }
  .contacts {
    position: absolute; left: 30px; top: 238px;
    list-style: none; font-size: 12px; color: var(--ink-soft);
  }
  .contacts li { display: flex; align-items: center; gap: 8px; height: 18px; }
  .contacts svg { width: 11px; height: 11px; flex: none; }
  /* Back */
  .card-back { left: 620px; background: var(--card-black); }
  .back-pattern {
    position: absolute; inset: 0;
    background: radial-gradient(circle at 40% 40%, var(--pattern-tone), var(--card-black) 75%);
  }
  .back-brand {
    position: absolute; left: 0; right: 0; top: 84px;
    text-align: center; color: var(--on-dark); font-weight: 700;
  }
  .back-brand .square {
    width: 50px; height: 50px; margin: 0 auto 14px;
    border: 5px solid var(--on-dark);
  }
  .back-brand .main { font-size: 24px; letter-spacing: 0.5px; display: block; }
  .back-brand .sub { font-size: 11px; letter-spacing: 7px; margin-right: -7px; display: block; margin-top: 3px; }
</style>
</head>
<body>
  <section class="card card-front">
    <div class="name-band">
      <p class="holder-name">KELVAN JOSHI</p>
      <p class="holder-title">Designated Partner</p>
    </div>
    <div class="brand-square"></div>
    <div class="grey-block"></div>
    <div class="company-name">
      <span class="main">GREYMARSH</span>
      <span class="sub">CONTRACTS</span>
    </div>
    <address class="address">
      <span class="firm">Greymarsh Engineering Contracts LLP</span>
      Block No.317, Wing C<br>
      Tulvo Trade Court, Manek Pural Road<br>
      Ruparel Industrial Estate<br>
      Goregaon(E), Mumbai - 400 063
    </address>
    <ul class="contacts">
      <li>
        <svg viewBox="0 0 12 12"><circle cx="6" cy="6" r="6" fill="#333"/><path d="M4 3.2c.4-.3.8-.2 1 .2l.4.8c.1.3 0 .6-.2.8l-.3.2c.3.6.8 1.1 1.4 1.4l.2-.3c.2-.2.5-.3.8-.2l.8.4c.4.2.5.6.2 1-.5.7-1.3.8-2.1.3A6 6 0 0 1 3.6 5.3c-.4-.8-.3-1.6.4-2.1z" fill="#fff"/></svg>
        +91 97415 60382
      </li>
      <li>
        <svg viewBox="0 0 12 12"><rect x="0" y="2" width="12" height="8" fill="#333"/><path d="M0.5 2.5 6 6.5l5.5-4" stroke="#fff" stroke-width="1" fill="none"/></svg>
        kelvanjoshi@mailbrook.example
      </li>
      <li>
        <svg viewBox="0 0 12 12"><circle cx="6" cy="6" r="6" fill="#333"/><circle cx="6" cy="6" r="3.6" stroke="#fff" stroke-width="0.8" fill="none"/><path d="M2.4 6h7.2M6 2.4v7.2" stroke="#fff" stroke-width="0.8"/></svg>
        www.greymarshcontracts.example
      </li>
    </ul>
  </section>

  <section class="card card-back">
    <div class="back-pattern" role="img" aria-label="Repeating embossed brand-mark pattern in dark grey tones"></div>
    <div class="back-brand">
      <div class="square"></div>
      <span class="main">GREYMARSH</span>
      <span class="sub">CONTRACTS</span>
    </div>
  </section>
</body>
</html>
```